Brightmoor - a website to encourage people to spend time in nature

I have a squarespace site with some content on it but the squarespace template doesn't completely suit my needs, I keep fiddling with the template but actually I need some professional help to get it looking the way I want and with the right 'mood'.
The website is for "Brightmoor" - it will be a blog where I write about the importance of nature for good health. I also want to use the website to market services such as outdoor coaching, retreats and walking workshops.
This has been in my head for a LONG time and I currently only use instagram for micro-blogs but it's time for me to get this moving. I've previously engaged other designers on branding for it but they just didn't get it quite the way that I wanted it and I wasn't completely happy with the results. It's been a process for me as to what I want but in the meantime I just didn't come back to the design aspect of it now. I'm looking for a designer who understands the purpose of the website, the ethos and can help me realise this into a design that's clean, clear and simple.

Please note that I have a domain (brightmoor.org) and a lot of content drafted on squarespace already. I have published it with password protection - password is brightmoor2020 - it still has some of the original template on it, but does have some content. Don't take it as anything to follow in particular, i am looking for fresh eyes and fresh ideas.

Target Market(s)

There are three main groups that I want to target - people who are suffering from stress and anxiety, people who treat them and parents who want to get their kids outside (thereby preventing stress and anxiety)

Contact Information for Business Card

Joan Petrie
Brightmoor
Telephone +44 7700 900417
brightmoor@mailvane.com

Logo Text

Brightmoor - if that. I have an idea that the logo should have a leaf on it somewhere, or maybe just be a leaf.

Coding

Coded - Design and coding required

Number of Pages Required

5+ page

Font styles to use
Serif
Sans Serif

Colors
add136
33b8a4
34a6d7
3377b5

Requirements
Must have
• Space for lots of images. The ability for me to edit the pages if I need to. Be user friendly. Look beautiful.
• For an idea of the images I use and the content I'm interested in writing about have a look at @brightmoor on instagram.
• That pop up about cookies so I am complying with data laws.
Should not have
• Must not be too 'busy' I'd like to avoid too much movement.

```html
<!DOCTYPE html>
<html lang="en">
<head>
<meta charset="utf-8">
<title>Brightmoor – Home</title>
<link href="https://fonts.googleapis.com/css2?family=Alegreya:ital,wght@0,400;1,400&family=Kaushan+Script&family=Open+Sans:wght@400;700&display=swap" rel="stylesheet">
<style>
:root{
  --teal:#33b8a4;
  --blue:#34a6d7;
  --ink:#2b2b2b;
  --body:#555;
  --white:#fff;
  --footer:#2e2e2f;
  --footer-deep:#202021;
  --footer-text:#d8d8d8;
}
*{margin:0;padding:0;box-sizing:border-box}
h1,h2,h3,h4{font-weight:400}
html,body{width:1200px;height:2200px;overflow:hidden;background:var(--white)}
body{position:relative;font-family:"Open Sans",Arial,sans-serif;color:var(--body)}
.page{position:absolute;top:148px;width:506px;height:1730px;transform:scale(1.1);transform-origin:0 0;background:var(--white);overflow:hidden}
.page--plain{left:30px}
.page--cookie{left:613px}
.page > *{position:absolute}

/* header */
.site-nav{left:0;top:0;width:506px;height:38px;background:rgba(255,255,255,.92);z-index:2}
.brand{position:absolute;left:38px;top:14px;font-family:"Alegreya",Georgia,serif;font-size:13px;color:var(--teal)}
.menu{position:absolute;left:157px;top:14px;display:flex;gap:13px;font-family:"Alegreya",Georgia,serif;font-style:italic;font-size:7px;color:var(--ink)}
.menu .is-active{color:var(--teal)}
.social{position:absolute;display:flex;gap:13px}
.social span{width:5px;height:5px;border-radius:50%;background:var(--ink)}
.site-nav .social{left:420px;top:16px}

/* photo areas */
.photo{display:block}
.hero-photo{left:0;top:0;width:506px;height:237px;background:linear-gradient(100deg,#252d1d 0%,#4d5c34 30%,#9fb27a 55%,#5f7a37 75%,#2b3520 100%)}
.band-education{left:0;top:405px;width:506px;height:238px;background:radial-gradient(circle at 22% 55%,#a3261d 0%,#6a2218 18%,transparent 38%),linear-gradient(120deg,#2a3a26,#1c2a1e 60%,#34502f)}
.band-connect{left:0;top:982px;width:506px;height:239px;background:radial-gradient(circle at 55% 45%,#4a3320 0%,transparent 20%),linear-gradient(130deg,#2b3c2c,#22301f 50%,#3e553a)}
.band-shade{left:0;width:506px;background:rgba(10,20,10,.35)}

/* hero text */
.hero-tagline{left:38px;top:100px;font-family:"Alegreya",Georgia,serif;font-size:15px;color:var(--white)}
.hero-title{left:36px;top:118px;font-family:"Kaushan Script",cursive;font-size:44px;color:var(--white);line-height:1}

/* section titles */
.script-title{left:0;width:506px;text-align:center;font-family:"Kaushan Script",cursive;color:var(--ink);line-height:1}
.script-title em{font-style:normal;color:var(--teal)}
.script-title--light{color:var(--white);font-size:28px}
.lead{left:0;width:506px;text-align:center;font-size:6.5px;line-height:12.5px}
.lead--light{color:var(--white)}
.pill{height:23px;border-radius:12px;border:1px solid var(--blue);color:var(--blue);font-size:6.5px;display:flex;align-items:center;justify-content:center;background:transparent}
.pill--light{border-color:var(--white);color:var(--white)}

/* how it works */
.card{top:713px;width:111px}
.card-photo{width:111px;height:74px}
.card-title{margin-top:9px;font-family:"Alegreya",Georgia,serif;font-style:italic;font-size:9px;color:var(--teal)}
.card-text{margin-top:3px;font-size:6.3px;line-height:14.3px;text-align:justify;color:var(--body)}

/* team */
.member{top:1254px;width:110px}
.member-name{font-family:"Alegreya",Georgia,serif;font-size:11px;color:var(--ink)}
.member-role{margin-top:7px;font-size:6px;font-weight:700;color:var(--blue)}
.member-text{margin-top:6px;font-size:6.3px;line-height:12px;text-align:justify;color:var(--body)}
.gallery-photo{top:1413px;width:173px;height:115px}

/* footer */
.site-footer{left:0;top:1565px;width:506px;height:165px;background:var(--footer);color:var(--footer-text)}
.site-footer > *{position:absolute}
.foot-head{font-family:"Alegreya",Georgia,serif;font-style:italic;font-size:9px;color:var(--footer-text);top:31px}
.foot-list{top:51px;list-style:none;font-size:5.5px;line-height:11.3px}
.newsletter-note{left:350px;top:51px;font-size:5.5px}
.signup{left:350px;top:69px;width:118px;height:15px;border:1px solid var(--blue);border-radius:8px;background:var(--white);overflow:hidden}
.signup-field{position:absolute;left:8px;top:4px;font-size:4.5px;color:#999}
.signup-btn{position:absolute;right:0;top:0;width:47px;height:13px;background:var(--blue);color:var(--white);font-size:5px;display:flex;align-items:center;justify-content:center;border-radius:7px}
.site-footer .social{left:351px;top:106px;gap:10px}
.site-footer .social span{background:var(--footer-text)}
.hours{left:0;top:129px;width:506px;text-align:center;font-size:5px}
.copyright{left:0;top:143px;width:506px;height:22px;background:var(--footer-deep);font-size:5px;display:flex;align-items:center;justify-content:center}

/* cookie */
.dim{left:0;top:0;width:506px;height:1730px;background:rgba(0,0,0,.62);z-index:5}
.cookie{left:131px;top:34px;width:243px;height:250px;z-index:6}
.cookie > *{position:absolute}
.cookie svg{left:0;top:0}
.cookie-title{left:0;top:76px;width:243px;text-align:center;font-family:"Alegreya",Georgia,serif;font-size:17px;line-height:20px;color:var(--ink)}
.cookie-text{left:22px;top:106px;width:199px;text-align:center;font-family:"Alegreya",Georgia,serif;font-style:italic;font-size:6px;line-height:13.5px;color:var(--ink)}
.cookie-actions{left:52px;top:171px;display:flex;gap:6px}
.cookie-actions .pill{width:66px;background:var(--white);border-color:var(--teal);color:var(--teal)}
</style>
</head>
<body>

<!-- page: home -->
<main class="page page--plain">
  <div class="photo hero-photo" role="img" aria-label="Sunlit forest path between tall trees"></div>
  <header class="site-nav">
    <div class="brand">Brightmoor</div>
    <nav class="menu"><span class="is-active">Home</span><span>About Us</span><span>Services</span><span>Coaching</span><span>Gallery</span><span>Blog</span><span>Contact Us</span></nav>
    <div class="social"><span></span><span></span><span></span></div>
  </header>
  <p class="hero-tagline">Nature for good health</p>
  <h1 class="hero-title">Brightmoor</h1>

  <h2 class="script-title" style="top:281px;font-size:18px">Welcome To <em>Brightmoor</em></h2>
  <p class="lead" style="top:311px">Our aim is to help people connect with nature as a means to feeling better.<br>We do this in a number of ways.</p>
  <div class="pill" style="left:216px;top:345px;width:74px">Find Out More</div>

  <div class="photo band-education" role="img" aria-label="Red holly berries among glossy dark leaves"></div>
  <div class="band-shade" style="top:405px;height:238px"></div>
  <h2 class="script-title script-title--light" style="top:470px">Education</h2>
  <p class="lead lead--light" style="top:515px">Start 'em young. Children have an intuitive connection with nature.<br>Watch a young child in a garden and you'll spot the fascination they have.</p>
  <div class="pill pill--light" style="left:214px;top:552px;width:78px">Learn More</div>

  <h2 class="script-title" style="top:686px;font-size:17px">How It <em>Works</em></h2>
  <article class="card" style="left:73px"><div class="photo card-photo" role="img" aria-label="Coastal path with a dog walking" style="background:linear-gradient(180deg,#8d9aa3,#5d6a4d 55%,#434b3c)"></div><h3 class="card-title">Coaching</h3><p class="card-text">Only one thing better than coaching and that's coaching in the great outdoors. We believe that being out in nature gives you a greater sense of perspective...</p></article>
  <article class="card" style="left:197px"><div class="photo card-photo" role="img" aria-label="Child looking out to sea, seen from behind" style="background:linear-gradient(180deg,#c9d3d8,#8fa1ab 60%,#6a6456)"></div><h3 class="card-title">Writing/speaking</h3><p class="card-text">Two sides of the same coin as far as we're concerned. The main driver is getting a message out that time in nature is good for you. We can provide copy for internal...</p></article>
  <article class="card" style="left:320px"><div class="photo card-photo" role="img" aria-label="Pink cherry blossom" style="background:radial-gradient(circle at 40% 40%,#f5b9cb,#d9567c 60%,#a52f50)"></div><h3 class="card-title">Retreat</h3><p class="card-text">Sometimes you just need to get away from it all. And that's where Brightmoor retreats come in. Our retreats are based at Heathfold Cottage located at the foot of the Carrow Hills...</p></article>
  <div class="pill" style="left:221px;top:922px;width:63px">Read More</div>

  <div class="photo band-connect" role="img" aria-label="Ladybird on large green leaves"></div>
  <div class="band-shade" style="top:982px;height:239px"></div>
  <h2 class="script-title script-title--light" style="top:1050px">Connecting To Nature</h2>
  <p class="lead lead--light" style="top:1093px">For kids, that can be learning in an outdoor setting, playing in the forest, having the<br>freedom to roam and explore all the wonders of nature.</p>
  <div class="pill pill--light" style="left:214px;top:1130px;width:78px">Learn More</div>

  <div class="member" style="left:73px"><h3 class="member-name">Lena Ashby</h3><p class="member-role">LOREM IPSUM</p><p class="member-text">Lorem ipsum dolor sit amet, tetur adipiscing elit, sed do eiusmod tempor incididunt ut labore et dolore magna aliqua. Ut enim ad minim veniam, quis nostrud tion ullamco laboris nisi ut aliquip ex ea commodo consequat.</p></div>
  <div class="member" style="left:198px"><h3 class="member-name">Owen Marsh</h3><p class="member-role">LOREM IPSUM</p><p class="member-text">Lorem ipsum dolor sit amet, tetur adipiscing elit, sed do eiusmod tempor incididunt ut labore et dolore magna aliqua. Ut enim ad minim veniam, quis nostrud tion ullamco laboris nisi ut aliquip ex ea commodo consequat.</p></div>
  <div class="member" style="left:320px"><h3 class="member-name">Nia Holt</h3><p class="member-role">LOREM IPSUM</p><p class="member-text">Lorem ipsum dolor sit amet, tetur adipiscing elit, sed do eiusmod tempor incididunt ut labore et dolore magna aliqua. Ut enim ad minim veniam, quis nostrud tion ullamco laboris nisi ut aliquip ex ea commodo consequat.</p></div>

  <div class="photo gallery-photo" style="left:73px;background:radial-gradient(circle at 50% 50%,#7c8f2a,#3e5520 60%,#26361a)" role="img" aria-label="Bed of small yellow flowers and green leaves"></div>
  <div class="photo gallery-photo" style="left:259px;background:radial-gradient(circle at 45% 45%,#8c88d0,#5a67a8 50%,#4d6d32)" role="img" aria-label="Butterfly on blue hydrangea blossoms"></div>

  <footer class="site-footer">
    <h4 class="foot-head" style="left:38px">Links</h4>
    <ul class="foot-list" style="left:38px"><li>Home</li><li>About Us</li><li>Services</li><li>Coaching</li><li>Gallery</li><li>Blog</li><li>Contact Us</li></ul>
    <h4 class="foot-head" style="left:128px">Legal</h4>
    <ul class="foot-list" style="left:128px"><li>Faq</li><li>Privacy Policy</li><li>Testimonials</li></ul>
    <h4 class="foot-head" style="left:222px">Contact Us</h4>
    <ul class="foot-list" style="left:222px"><li>24 Fernlea Row, London,</li><li>Islington N7 4QT</li><li>Phone: 020 7946 0321</li><li>Email: hello@brightmoor.org</li></ul>
    <h4 class="foot-head" style="left:350px">Newsletter</h4>
    <p class="newsletter-note">Subscribe Our Newsletter For More Info</p>
    <div class="signup"><span class="signup-field">Email Address</span><span class="signup-btn">Subscribe</span></div>
    <div class="social"><span></span><span></span><span></span></div>
    <p class="hours">Opening Hours : Monday – Friday, 8:00 a.m. – 5:00 p.m.</p>
    <p class="copyright">© 2020 Copyrights The Company Name All Rights Reserved</p>
  </footer>
</main>

<!-- page: home with cookie notice -->
<main class="page page--cookie">
  <div class="photo hero-photo" role="img" aria-label="Sunlit forest path between tall trees"></div>
  <header class="site-nav">
    <div class="brand">Brightmoor</div>
    <nav class="menu"><span class="is-active">Home</span><span>About Us</span><span>Services</span><span>Coaching</span><span>Gallery</span><span>Blog</span><span>Contact Us</span></nav>
    <div class="social"><span></span><span></span><span></span></div>
  </header>
  <p class="hero-tagline">Nature for good health</p>
  <h1 class="hero-title">Brightmoor</h1>

  <h2 class="script-title" style="top:281px;font-size:18px">Welcome To <em>Brightmoor</em></h2>
  <p class="lead" style="top:311px">Our aim is to help people connect with nature as a means to feeling better.<br>We do this in a number of ways.</p>
  <div class="pill" style="left:216px;top:345px;width:74px">Find Out More</div>

  <div class="photo band-education" role="img" aria-label="Red holly berries among glossy dark leaves"></div>
  <div class="band-shade" style="top:405px;height:238px"></div>
  <h2 class="script-title script-title--light" style="top:470px">Education</h2>
  <p class="lead lead--light" style="top:515px">Start 'em young. Children have an intuitive connection with nature.<br>Watch a young child in a garden and you'll spot the fascination they have.</p>
  <div class="pill pill--light" style="left:214px;top:552px;width:78px">Learn More</div>

  <h2 class="script-title" style="top:686px;font-size:17px">How It <em>Works</em></h2>
  <article class="card" style="left:73px"><div class="photo card-photo" role="img" aria-label="Coastal path with a dog walking" style="background:linear-gradient(180deg,#8d9aa3,#5d6a4d 55%,#434b3c)"></div><h3 class="card-title">Coaching</h3><p class="card-text">Only one thing better than coaching and that's coaching in the great outdoors. We believe that being out in nature gives you a greater sense of perspective...</p></article>
  <article class="card" style="left:197px"><div class="photo card-photo" role="img" aria-label="Child looking out to sea, seen from behind" style="background:linear-gradient(180deg,#c9d3d8,#8fa1ab 60%,#6a6456)"></div><h3 class="card-title">Writing/speaking</h3><p class="card-text">Two sides of the same coin as far as we're concerned. The main driver is getting a message out that time in nature is good for you. We can provide copy for internal...</p></article>
  <article class="card" style="left:320px"><div class="photo card-photo" role="img" aria-label="Pink cherry blossom" style="background:radial-gradient(circle at 40% 40%,#f5b9cb,#d9567c 60%,#a52f50)"></div><h3 class="card-title">Retreat</h3><p class="card-text">Sometimes you just need to get away from it all. And that's where Brightmoor retreats come in. Our retreats are based at Heathfold Cottage located at the foot of the Carrow Hills...</p></article>
  <div class="pill" style="left:221px;top:922px;width:63px">Read More</div>

  <div class="photo band-connect" role="img" aria-label="Ladybird on large green leaves"></div>
  <div class="band-shade" style="top:982px;height:239px"></div>
  <h2 class="script-title script-title--light" style="top:1050px">Connecting To Nature</h2>
  <p class="lead lead--light" style="top:1093px">For kids, that can be learning in an outdoor setting, playing in the forest, having the<br>freedom to roam and explore all the wonders of nature.</p>
  <div class="pill pill--light" style="left:214px;top:1130px;width:78px">Learn More</div>

  <div class="member" style="left:73px"><h3 class="member-name">Lena Ashby</h3><p class="member-role">LOREM IPSUM</p><p class="member-text">Lorem ipsum dolor sit amet, tetur adipiscing elit, sed do eiusmod tempor incididunt ut labore et dolore magna aliqua. Ut enim ad minim veniam, quis nostrud tion ullamco laboris nisi ut aliquip ex ea commodo consequat.</p></div>
  <div class="member" style="left:198px"><h3 class="member-name">Owen Marsh</h3><p class="member-role">LOREM IPSUM</p><p class="member-text">Lorem ipsum dolor sit amet, tetur adipiscing elit, sed do eiusmod tempor incididunt ut labore et dolore magna aliqua. Ut enim ad minim veniam, quis nostrud tion ullamco laboris nisi ut aliquip ex ea commodo consequat.</p></div>
  <div class="member" style="left:320px"><h3 class="member-name">Nia Holt</h3><p class="member-role">LOREM IPSUM</p><p class="member-text">Lorem ipsum dolor sit amet, tetur adipiscing elit, sed do eiusmod tempor incididunt ut labore et dolore magna aliqua. Ut enim ad minim veniam, quis nostrud tion ullamco laboris nisi ut aliquip ex ea commodo consequat.</p></div>

  <div class="photo gallery-photo" style="left:73px;background:radial-gradient(circle at 50% 50%,#7c8f2a,#3e5520 60%,#26361a)" role="img" aria-label="Bed of small yellow flowers and green leaves"></div>
  <div class="photo gallery-photo" style="left:259px;background:radial-gradient(circle at 45% 45%,#8c88d0,#5a67a8 50%,#4d6d32)" role="img" aria-label="Butterfly on blue hydrangea blossoms"></div>

  <footer class="site-footer">
    <h4 class="foot-head" style="left:38px">Links</h4>
    <ul class="foot-list" style="left:38px"><li>Home</li><li>About Us</li><li>Services</li><li>Coaching</li><li>Gallery</li><li>Blog</li><li>Contact Us</li></ul>
    <h4 class="foot-head" style="left:128px">Legal</h4>
    <ul class="foot-list" style="left:128px"><li>Faq</li><li>Privacy Policy</li><li>Testimonials</li></ul>
    <h4 class="foot-head" style="left:222px">Contact Us</h4>
    <ul class="foot-list" style="left:222px"><li>24 Fernlea Row, London,</li><li>Islington N7 4QT</li><li>Phone: 020 7946 0321</li><li>Email: hello@brightmoor.org</li></ul>
    <h4 class="foot-head" style="left:350px">Newsletter</h4>
    <p class="newsletter-note">Subscribe Our Newsletter For More Info</p>
    <div class="signup"><span class="signup-field">Email Address</span><span class="signup-btn">Subscribe</span></div>
    <div class="social"><span></span><span></span><span></span></div>
    <p class="hours">Opening Hours : Monday – Friday, 8:00 a.m. – 5:00 p.m.</p>
    <p class="copyright">© 2020 Copyrights The Company Name All Rights Reserved</p>
  </footer>

  <div class="dim"></div>
  <section class="cookie" aria-label="Cookie policy notice">
    <svg width="243" height="250" viewBox="0 0 243 250" aria-hidden="true">
      <g fill="var(--teal)">
        <circle cx="121.5" cy="125" r="97"/>
        <circle cx="121.5" cy="38" r="39"/><circle cx="183" cy="63" r="39"/>
        <circle cx="204" cy="125" r="39"/><circle cx="183" cy="187" r="39"/>
        <circle cx="121.5" cy="212" r="39"/><circle cx="60" cy="187" r="39"/>
        <circle cx="39" cy="125" r="39"/><circle cx="60" cy="63" r="39"/>
      </g>
      <g fill="var(--white)">
        <circle cx="121.5" cy="125" r="94"/>
        <circle cx="121.5" cy="38" r="36"/><circle cx="183" cy="63" r="36"/>
        <circle cx="204" cy="125" r="36"/><circle cx="183" cy="187" r="36"/>
        <circle cx="121.5" cy="212" r="36"/><circle cx="60" cy="187" r="36"/>
        <circle cx="39" cy="125" r="36"/><circle cx="60" cy="63" r="36"/>
      </g>
    </svg>
    <h2 class="cookie-title">Our Cookie Policy</h2>
    <p class="cookie-text">Lorem ipsum dolor sit amet, consectetur adipiscing elit, sed do eiusmod tempor incididunt ut labore et dolore magna aliqua. Ut enim ad minim veniam, quis nostrud exercitation ullamco laboris nisi ut aliquip ex ea commodo consequat.</p>
    <div class="cookie-actions"><div class="pill">Accept</div><div class="pill">Decline</div></div>
  </section>
</main>

</body>
</html>
```